CANNABIS BASED BUSINESS CARD DESIGN AND CREATION

WE ARE A PRIVATELY OWNED INVESTMENT CORPORATION. WE PRIMARILY INVEST IN LEGAL PUBLICALLY TRADED CANNABIS COMPANIES THAT ARE TRADED THROUGH THE OTC OR VOLTRIX. WE OFFER THE PUBLIC AN OPPORTUNITY TO PARTICIPATE DIRECTLY WITH THESE COMPANIES FOR NO FEES, NO COMMISSIONS AND IN DEPTH RESEARCH ON EVERY COMPANY PROFILE. WE ARE ALSO PRO FEDERAL LEGALIZATION AND WILL APPLY FOR CULTIVATION AND DISPENSARY LICENSES WHEN THEY BECOME AVAILABLE.

Target Market(s)

30-60 FEMALE AND MALE INVESTORS

Industry/Entity Type

Business

Contact Information for Business Card

EDS CAPITAL GROUP CORPERIN D SLAUGHTER(469) 426-6302ERIN@EDSCAPITALGROUP.COM

Font styles to use
Decorative

Requirements
Must have
• COMPANY LOGO
• CANNABIS LOGO
Nice to have
• MODERN FONT AND LOGOS

```html
<!DOCTYPE html>
<html lang="en">
<head>
<meta charset="utf-8">
<title>TQM Capital Group Corp – Business Card</title>
<link href="https://fonts.googleapis.com/css2?family=Lato:wght@400;700&display=swap" rel="stylesheet">
<style>
  :root {
    --backdrop: #6e7c14;
    --card-dark: #050505;
    --card-mid: #1b1b1b;
    --brand-green: #2fb24a;
    --icon-green: #27a043;
    --text-light: #f2f2f2;
    --text-muted: #a9a9a9;
    --rule: #2e2e2e;
    --leaf-shade: rgba(70,70,70,.35);
  }
  * { box-sizing: border-box; margin: 0; padding: 0; }
  html, body {
    width: 1200px; height: 900px; overflow: hidden;
    background: var(--backdrop);
    font-family: "Lato", Arial, sans-serif;
  }
  .stage { position: relative; width: 1200px; height: 900px; }

  .card {
    position: absolute;
    width: 620px; height: 360px;
    background: radial-gradient(ellipse at 45% 40%, var(--card-mid) 0%, var(--card-dark) 70%);
    box-shadow: 0 10px 26px rgba(0,0,0,.35);
    overflow: hidden;
  }
  .card--front { left: 90px; top: 80px; }
  .card--back  { left: 490px; top: 460px; }

  .leaf-decoration {
    position: absolute;
    left: 380px; top: 20px; width: 240px; height: 290px;
    background: radial-gradient(ellipse at center, var(--leaf-shade) 0%, rgba(40,40,40,0) 70%);
  }

  .wordmark {
    display: flex; align-items: center; gap: 12px;
    color: var(--brand-green); font-weight: 400; letter-spacing: 2px;
    white-space: nowrap;
  }
  .wordmark__dot { border-radius: 50%; background: var(--brand-green); flex: none; }

  .card--front .wordmark {
    position: absolute; left: 0; right: 0; top: 160px;
    justify-content: center; font-size: 28px;
  }
  .card--front .wordmark__dot { width: 22px; height: 22px; }

  .card--back .wordmark {
    position: absolute; right: 40px; top: 70px; font-size: 19px;
  }
  .card--back .wordmark__dot { width: 14px; height: 14px; }

  .rule-top {
    position: absolute; right: 40px; top: 128px;
    width: 300px; height: 1px; background: var(--rule);
  }

  .holder {
    position: absolute; left: 40px; top: 262px;
    color: var(--text-light); font-size: 17px; letter-spacing: .5px;
  }
  .holder::after {
    content: ""; display: block; margin-top: 10px;
    width: 270px; height: 1px; background: var(--rule);
  }

  .contacts {
    position: absolute; left: 340px; top: 224px;
    list-style: none; color: var(--text-muted); font-size: 12.5px;
  }
  .contacts li { display: flex; align-items: center; gap: 10px; height: 22px; white-space: nowrap; }
  .contacts svg { width: 13px; height: 13px; fill: var(--icon-green); flex: none; }
</style>
</head>
<body>
<main class="stage">

  <section class="card card--front" aria-label="Business card front">
    <div class="leaf-decoration" role="img" aria-label="Faint leaf decoration"></div>
    <div class="wordmark"><span class="wordmark__dot"></span>TQM CAPITAL GROUP CORP</div>
  </section>

  <section class="card card--back" aria-label="Business card back">
    <div class="wordmark"><span class="wordmark__dot"></span>TQM CAPITAL GROUP CORP</div>
    <div class="rule-top"></div>

    <p class="holder">MARLA J PENDLEBURY</p>

    <ul class="contacts">
      <li>
        <svg viewBox="0 0 16 16" aria-hidden="true"><path d="M2 6c0-2 2-3 6-3s6 1 6 3l-3 1-1-2H6L5 7 2 6zm2 2h8l1 6H3l1-6zm4 1.5a2 2 0 100 4 2 2 0 000-4z"/></svg>
        (555) 013-4478
      </li>
      <li>
        <svg viewBox="0 0 16 16" aria-hidden="true"><path d="M1 3h14v10H1V3zm1.5 1.5v.3L8 9l5.5-4.2v-.3h-11zM2.5 6.6v4.9h11V6.6L8 10.8 2.5 6.6z"/></svg>
        marla@tqmcapitalgroup-demo.com
      </li>
      <li>
        <svg viewBox="0 0 16 16" aria-hidden="true"><path d="M6.5 9.5l3-3 1 1-3 3-1-1zM4 9l1.2 1.2-1 1a1.1 1.1 0 001.6 1.6l1-1L8 13l-1 1a2.8 2.8 0 01-4-4l1-1zm8-2l-1.2-1.2 1-1a1.1 1.1 0 00-1.6-1.6l-1 1L8 3l1-1a2.8 2.8 0 014 4l-1 1z"/></svg>
        www.harrowfield-demo.com
      </li>
    </ul>
  </section>

</main>
</body>
</html>
```